Telecommunications Company needs a business card design

We are looking for a sleek, professional and modern business card design based off our new logo. Will look at both light and dark options. On some designs please provide a small space for a QR code

Target Market(s)

B2B clients in Australia

Contact Information for Business Card

Name, Position, Brisbane (head) office, Phone number, email address, QR code (link to our website qlinetelecom.com.au

Colors
0054AA
0677BA
7BADD7
CADEEF
E8F1F8
0094D4
00A9DD
6FCCEA
C7EBF8
E9F6FB
00AB8E
00BBA5
67D7C9
C6EFE9
E9F9F6

```html
<!DOCTYPE html>
<html lang="en">
<head>
<meta charset="utf-8">
<title>Qline Telecom – Business Card</title>
<link href="https://fonts.googleapis.com/css2?family=Poppins:wght@400;500;600&display=swap" rel="stylesheet">
<style>
  :root {
    --page-bg: #e6e8ea;
    --card-bg: #f5f7f9;
    --ink-dark: #3a3d42;
    --ink-grey: #4a4e54;
    --brand-navy: #1d4f86;
    --brand-teal: #0d6e78;
    --web-light: #cfe6ec;
    --divider: #5b6470;
    --rule-line: #4a4e54;
  }
  html, body {
    margin: 0;
    padding: 0;
    width: 1200px;
    height: 970px;
    overflow: hidden;
    background: var(--page-bg);
  }
  .canvas {
    position: relative;
    width: 1200px;
    height: 970px;
  }
  .card {
    position: absolute;
    left: 100px;
    top: 201px;
    width: 1000px;
    height: 568px;
    background: var(--card-bg);
    border-radius: 24px;
    overflow: hidden;
    box-shadow: 0 10px 30px rgba(0,0,0,0.12);
    font-family: "Poppins", sans-serif;
  }
  .card-band {
    position: absolute;
    left: 0;
    bottom: 0;
    width: 1000px;
    height: 150px;
  }
  .brand-name {
    position: absolute;
    left: 80px;
    top: 200px;
    width: 330px;
    margin: 0;
    font-size: 52px;
    line-height: 1.1;
    font-weight: 600;
    color: var(--brand-navy);
    text-align: center;
  }
  .divider {
    position: absolute;
    left: 451px;
    top: 154px;
    width: 2px;
    height: 214px;
    background: var(--divider);
  }
  .contact {
    position: absolute;
    left: 496px;
    top: 142px;
    color: var(--ink-grey);
  }
  .person-name {
    margin: 0;
    font-size: 35px;
    line-height: 40px;
    font-weight: 500;
    color: var(--ink-dark);
    letter-spacing: 0.5px;
  }
  .person-role {
    margin: 0;
    font-size: 23px;
    line-height: 26px;
    color: var(--brand-navy);
  }
  .address {
    margin: 20px 0 0;
    font-style: normal;
    font-size: 23px;
    line-height: 34px;
  }
  .contact-list {
    list-style: none;
    margin: 12px 0 0;
    padding: 0;
    font-size: 23px;
    line-height: 34px;
  }
  .contact-list li {
    display: flex;
    align-items: center;
    gap: 8px;
  }
  .contact-icon {
    width: 28px;
    height: 28px;
    flex: none;
  }
  .website {
    position: absolute;
    right: 58px;
    bottom: 28px;
    margin: 0;
    font-size: 22px;
    color: var(--web-light);
  }
</style>
</head>
<body>
<main class="canvas">
  <section class="card" aria-label="Business card">
    <svg class="card-band" viewBox="0 0 1000 150" preserveAspectRatio="none" aria-hidden="true">
      <defs>
        <linearGradient id="bandGradient" x1="0" y1="0" x2="1" y2="0">
          <stop offset="0" stop-color="#1f5a97"/>
          <stop offset="1" stop-color="#0d6e78"/>
        </linearGradient>
      </defs>
      <path d="M0,55 Q500,0 1000,55 L1000,150 L0,150 Z" fill="url(#bandGradient)"/>
      <path d="M0,35 Q500,-18 1000,35" fill="none" stroke="var(--rule-line)" stroke-width="3"/>
    </svg>

    <h1 class="brand-name">Qline Telecom</h1>

    <div class="divider"></div>

    <div class="contact">
      <h2 class="person-name">LIAM CARTER</h2>
      <p class="person-role">Director</p>
      <address class="address">28 Harbour Street<br>Kelvin Grove</address>
      <ul class="contact-list">
        <li>
          <svg class="contact-icon" viewBox="0 0 28 28" aria-hidden="true">
            <circle cx="14" cy="14" r="13" fill="var(--brand-teal)"/>
            <circle cx="14" cy="14" r="10" fill="none" stroke="#fff" stroke-width="1.2"/>
            <path d="M10.5,8.5 l2,-0.5 l1.2,3 l-1.4,1 c0.6,1.6 1.6,2.6 3.2,3.2 l1,-1.4 l3,1.2 l-0.5,2 c-5,0.4 -8.9,-3.5 -8.5,-8.5 z" fill="#fff"/>
          </svg>
          <span>1300 555 214</span>
        </li>
        <li>
          <svg class="contact-icon" viewBox="0 0 28 28" aria-hidden="true">
            <circle cx="14" cy="14" r="13" fill="var(--brand-teal)"/>
            <circle cx="14" cy="14" r="10" fill="none" stroke="#fff" stroke-width="1.2"/>
            <rect x="8.5" y="10" width="11" height="8" rx="1" fill="none" stroke="#fff" stroke-width="1.4"/>
            <path d="M8.5,10.5 L14,15 L19.5,10.5" fill="none" stroke="#fff" stroke-width="1.4"/>
          </svg>
          <span>info@qlinetelecom.com.au</span>
        </li>
      </ul>
    </div>

    <p class="website">qlinetelecom.com.au</p>
  </section>
</main>
</body>
</html>
```